UX - Need some screens design for a Skill Assessment Application

I am building an app to carry out skill assessments. Depending on how the assessment is configured, it may have one or more parts
1. Question based assessment (Multiple Choice, True False, Fill in the blanks"
2. Endorsement by two colleagues - A screen that allows user to pick colleagues based on search and shows the status of pending requests
3. A written submission - a page that explains the format of the submission and a file upload
As each assessment can be configured with or without any of the steps, the assessment UI must be such that these areas get hidden/displayed based on configuration.
Colour codes to be used can be #0e78bb and #ffffff
There will also be a start screen (instructions) and an end screen (results)
Target Market(s)
Enterprise software
Number of Pages Required
4 page

```html
<!DOCTYPE html>
<html lang="en">
<head>
<meta charset="utf-8">
<title>Application Design Capabilities – Question 7</title>
<link href="https://fonts.googleapis.com/css2?family=Inter:wght@400;500;600;700&display=swap" rel="stylesheet">
<style>
:root{
  --brand-dark:#0055ab;
  --brand:#0e78bb;
  --link:#1a96d4;
  --white:#ffffff;
  --ink:#1f2328;
  --muted:#5b6168;
  --page:#f5f6f8;
  --line:#dcdfe3;
}
*{box-sizing:border-box;margin:0;padding:0}
html,body{width:1200px;height:686px;overflow:hidden}
body{font-family:'Inter',sans-serif;background:var(--page);color:var(--ink);position:relative}
.topbar{height:43px;background:var(--brand-dark);display:flex;align-items:center;padding:0 57px;color:var(--white)}
.brand{display:flex;align-items:center;gap:9px;font-size:14px;font-weight:500}
.brand-dot{width:20px;height:20px;border-radius:50%;background:var(--white)}
.nav{margin-left:auto;display:flex;align-items:center;gap:21px;font-size:12px}
.nav a{color:#d6e6f5;text-decoration:none}
.nav a.active{color:var(--white);font-weight:700}
.avatar{width:27px;height:27px;border-radius:50%;background:#cfe8f8;color:var(--ink);font-weight:700;font-size:12px;display:flex;align-items:center;justify-content:center;margin-left:0}
.header{background:var(--white);height:97px;position:relative;border-bottom:1px solid var(--line)}
.crumbs{position:absolute;left:56px;top:21px;display:flex;align-items:center;gap:10px;font-size:11.5px;color:var(--muted)}
.crumbs a{color:var(--link);text-decoration:none;margin-left:3px}
.updated{position:absolute;right:90px;top:25px;font-size:11.5px;color:var(--muted)}
.updated b{font-weight:500}
.title{position:absolute;left:88px;top:97px;transform:translateY(-100%);}
.title-row{position:absolute;left:88px;top:55px;display:flex;align-items:center;gap:14px}
.title-row h1{font-size:22px;font-weight:600}
.save{position:absolute;right:89px;top:53px;width:104px;height:31px;border:1px solid var(--brand);border-radius:2px;background:var(--white);color:var(--brand);font:500 11.5px 'Inter',sans-serif}
.meta{height:45px;background:#f1f2f4;border-bottom:1px solid var(--line);display:flex;align-items:center;padding-left:88px;font-size:10.5px;position:relative}
.meta .item{padding-right:21px;margin-right:21px;border-right:1px solid var(--line);line-height:14px}
.meta .item:last-of-type{border:none}
.meta .val{color:var(--link)}
.meta .grey{color:var(--muted)}
.progress{position:absolute;right:89px;top:7px;display:flex;align-items:center;gap:8px;font-size:10.5px;color:var(--muted)}
.progress b{color:var(--ink);font-weight:600}
.question{position:absolute;left:367px;top:220px;width:467px}
.q-head{display:flex;gap:21px;font-size:15px}
.q-num{color:var(--muted)}
.choices{margin:26px 0 0 47px;display:flex;gap:7px}
.choice{height:31px;padding:0 14px;border-radius:16px;font:500 11.5px 'Inter',sans-serif;border:1px solid var(--line);background:var(--white);color:var(--brand)}
.choice.selected{background:var(--brand);color:var(--white);border-color:var(--brand)}
.divider{border-top:1px solid var(--line);margin-top:28px}
.actions{display:flex;align-items:center;margin-top:28px}
.btn{height:31px;padding:0 14px;font:500 11.5px 'Inter',sans-serif;border-radius:2px}
.btn-outline{border:1px solid var(--brand);background:var(--white);color:var(--brand)}
.skip{margin-left:auto;margin-right:27px;font-size:11.5px;color:var(--muted);display:flex;align-items:center;gap:4px}
.btn-primary{background:var(--brand);color:var(--white);border:none;width:52px;padding:0}
</style>
</head>
<body>
<header class="topbar">
  <div class="brand"><span class="brand-dot"></span>Skillgrid</div>
  <nav class="nav">
    <a class="active" href="#">Assessments</a>
    <a href="#">Endorsement</a>
    <a href="#">Submissions</a>
    <a href="#">Results</a>
    <span class="avatar">D</span>
    <svg width="10" height="10" viewBox="0 0 10 10"><path d="M2 3.5l3 3 3-3" stroke="#fff" stroke-width="1.4" fill="none"/></svg>
  </nav>
</header>
<section class="header">
  <div class="crumbs">
    <svg width="20" height="20" viewBox="0 0 20 20"><circle cx="10" cy="10" r="9" stroke="#0e78bb" stroke-width="1.5" fill="none"/><path d="M14 10H6M9.5 6.5L6 10l3.5 3.5" stroke="#0e78bb" stroke-width="1.5" fill="none"/></svg>
    <a href="#">Assessment</a><span>/</span><span>Application Design Capabilities</span>
  </div>
  <div class="updated">Last Updated: <b>17/05/2024</b></div>
  <div class="title-row">
    <svg width="22" height="22" viewBox="0 0 22 22"><rect x="1.5" y="1.5" width="14" height="18" rx="1" stroke="#5b6168" stroke-width="1.5" fill="none"/><path d="M4.5 6h2M8 6h5M4.5 10h2M8 10h4M4.5 14h2" stroke="#5b6168" stroke-width="1.4"/><circle cx="15.5" cy="15" r="4" fill="#fff" stroke="#5b6168" stroke-width="1.4"/><path d="M13.8 15l1.2 1.2 2-2M18.3 18l2 2" stroke="#5b6168" stroke-width="1.4" fill="none"/></svg>
    <h1>Application Design Capabilities</h1>
  </div>
  <button class="save">Save Progress</button>
</section>
<section class="meta">
  <span class="item">Assessment Date: <span class="val">September 23, 2024</span></span>
  <span class="item">Assessment Type: <span class="val">UI/UX Skill</span></span>
  <span class="item">Assessment Responses: <span class="grey">6 of 8 Responded / Closed: in next 4 month</span></span>
  <div class="progress">
    <svg width="32" height="32" viewBox="0 0 32 32"><circle cx="16" cy="16" r="13.5" stroke="#e0e3e7" stroke-width="3" fill="none"/><circle cx="16" cy="16" r="13.5" stroke="#1aa3e0" stroke-width="3" fill="none" stroke-dasharray="74.2 84.8" transform="rotate(-90 16 16)"/></svg>
    <span><b>7</b> / 8</span>
  </div>
</section>
<main class="question">
  <div class="q-head"><span class="q-num">Q.7.</span><span>This is a single question with T/F choice</span></div>
  <div class="choices">
    <button class="choice selected">True</button>
    <button class="choice">False</button>
  </div>
  <div class="divider"></div>
  <div class="actions">
    <button class="btn btn-outline">Go Back</button>
    <span class="skip">Skip <svg width="8" height="8" viewBox="0 0 8 8"><path d="M2.5 1l3 3-3 3" stroke="#5b6168" stroke-width="1.3" fill="none"/></svg></span>
    <button class="btn btn-primary">Next</button>
  </div>
</main>
</body>
</html>
```